New Business Card Design Project LORVANTI-Italy

we are LORVANTI-Italy
our company in the market for 3 years we are luxury cosmetic company and its about time for a facelift :)
i will like to have elegant luxurious and unique business card
that will give the person that get it a unique, luxurious and elegant impression
I'm VERY OPEN FOR NEW IDEAS , even duo i add a few files of things that i see on line and i like them

i add my logo as well
my website is LORVANTI.COM
(if you would like to see the main style that we have)

Target Market(s)

adult that have money :)

Industry/Entity Type

Business

Contact Information for Business Card

Name - Dario Lorvanti
Position - CEO and CO Founder
address - 4817 E Halvern
telephone - 555-384-1926
email - dario@lorvanti.com
fax - 555-384-1926
website - LORVANTI.COM

Colors
000000
959595
fbee3e
ffffff

Requirements
Must have
• big logo in GOLD color
• elegant look
• impressive
Nice to have
• not must but maybe classy pattern background
• not must but maybe emblem
• maybe clear plastic business card
Should not have
• colors
• images

```html
<!DOCTYPE html>
<html lang="en">
<head>
<meta charset="utf-8">
<title>LORVANTI Italy – Business Card</title>
<link href="https://fonts.googleapis.com/css2?family=Cinzel:wght@400;700&family=Lato:wght@400;900&display=swap" rel="stylesheet">
<style>
  :root {
    --backdrop: #d9d9db;
    --card-black: #1e1c1a;
    --card-black-deep: #141311;
    --gold: #c9a846;
    --gold-light: #e4cd7e;
    --gold-dark: #9c7d2c;
    --ink-on-gold: #1a1712;
  }
  * { box-sizing: border-box; margin: 0; padding: 0; }
  html, body {
    width: 1200px;
    height: 803px;
    overflow: hidden;
    background: var(--backdrop);
  }
  .canvas {
    position: relative;
    width: 1200px;
    height: 803px;
  }
  .card {
    position: absolute;
    top: 62px;
    width: 400px;
    height: 680px;
    overflow: hidden;
    box-shadow: 0 10px 28px rgba(0, 0, 0, 0.35);
  }
  .card--front { left: 170px; }
  .card--back {
    left: 630px;
    background: linear-gradient(160deg, var(--card-black), var(--card-black-deep));
  }

  /* Front */
  .gold-field {
    position: absolute;
    inset: 0 0 218px 0;
    background: linear-gradient(150deg, var(--gold-dark) 0%, var(--gold-light) 45%, var(--gold) 70%, var(--gold-dark) 100%);
  }
  .front-mark {
    position: absolute;
    top: 0;
    left: 0;
    right: 0;
    height: 462px;
    display: flex;
    align-items: center;
    justify-content: center;
    gap: 14px;
    font-family: "Cinzel", serif;
    font-weight: 700;
    font-size: 34px;
    letter-spacing: 3px;
    color: var(--ink-on-gold);
  }
  .front-mark__dot {
    width: 26px;
    height: 26px;
    border: 3px solid var(--ink-on-gold);
    border-radius: 50%;
  }
  .name-band {
    position: absolute;
    left: 0;
    right: 0;
    bottom: 0;
    height: 218px;
    background: var(--card-black);
    display: flex;
    flex-direction: column;
    align-items: center;
    justify-content: center;
    font-family: "Cinzel", serif;
    color: var(--gold);
  }
  .name-band__word {
    font-size: 52px;
    font-weight: 400;
    letter-spacing: 2px;
    line-height: 1;
  }
  .name-band__rule {
    width: 300px;
    height: 2px;
    background: var(--gold);
    margin: 10px 0 8px;
  }
  .name-band__country {
    font-size: 20px;
    letter-spacing: 3px;
  }

  /* Back */
  .back-mark {
    margin-top: 70px;
    display: flex;
    align-items: center;
    justify-content: center;
    gap: 12px;
    font-family: "Cinzel", serif;
    font-weight: 700;
    font-size: 34px;
    letter-spacing: 3px;
    color: var(--gold);
  }
  .back-mark__dot {
    width: 24px;
    height: 24px;
    border: 3px solid var(--gold);
    border-radius: 50%;
  }
  .holder {
    margin-top: 48px;
    text-align: center;
    font-family: "Lato", sans-serif;
    color: var(--gold);
  }
  .holder__name {
    font-weight: 900;
    font-size: 30px;
    letter-spacing: 0.5px;
    text-transform: uppercase;
  }
  .holder__title {
    font-size: 17px;
    margin-top: 2px;
  }
  .contact-list {
    list-style: none;
    margin-top: 40px;
    text-align: center;
    font-family: "Lato", sans-serif;
    font-size: 17px;
    color: var(--gold);
  }
  .contact-list li { line-height: 1.3; }
  .contact-list .bullet {
    display: block;
    width: 10px;
    height: 8px;
    margin: 6px auto;
    background: var(--gold-light);
  }
  .address {
    margin-top: 30px;
    text-align: center;
    font-family: "Lato", sans-serif;
    font-size: 17px;
    color: var(--gold);
  }
</style>
</head>
<body>
<main class="canvas">

  <section class="card card--front" aria-label="Business card front">
    <div class="gold-field" role="img" aria-label="Gold foil field with a fine repeating diamond pattern"></div>
    <div class="front-mark">
      <span class="front-mark__dot"></span>
      <span>LORVANTI</span>
    </div>
    <div class="name-band">
      <span class="name-band__word">LORVANTI</span>
      <span class="name-band__rule"></span>
      <span class="name-band__country">ITALY</span>
    </div>
  </section>

  <section class="card card--back" aria-label="Business card back">
    <div class="back-mark">
      <span class="back-mark__dot"></span>
      <span>LORVANTI</span>
    </div>
    <div class="holder">
      <p class="holder__name">Dario Lorvanti</p>
      <p class="holder__title">CEO and CO Founder</p>
    </div>
    <ul class="contact-list">
      <li><span class="bullet"></span>555-384-1926</li>
      <li><span class="bullet"></span>555-384-1926</li>
      <li><span class="bullet"></span>dario@lorvanti.com</li>
      <li><span class="bullet"></span>LORVANTI.COM</li>
    </ul>
    <p class="address">4817 E Halvern</p>
  </section>

</main>
</body>
</html>
```